Corporate Brochure Cover Design

We need a design for a corporate A4 Size portfolio cover (front and back) which we will be distributing. to our commercial clients.

We are a professional plumbing company that is an industry leader for service we provide to our clients and technology we use. The design needs to incorporate the colours black, red, white and silver and needs to include our logo. We dont have any slogans or mottos... If you wanted to use something it could be "Delivering exceptional service...Always!" however i dont want it to b the focal point of the cover.

Im looking for something professional and modern that has the WOW factor!

Size is A4 - both front and back covers. You can include pictures as well or sample pictures of where we can source and put our own team pictures.

if you have any questions, please do not hesitate to contact me.

Target Market(s)

Our commercial & strata clients - professional industry.

Industry/Entity Type

Commercial

Font styles to use
Sans Serif

Requirements
Must have
• Red, black, white, silver as the colour scheme.
• Include the logo.
Nice to have
• Modern design and something that makes the client go WOW before they open the brochure.
Should not have
• lots of text

```html
<!DOCTYPE html>
<html lang="en">
<head>
<meta charset="UTF-8">
<title>TruFlow – Brochure Back Cover</title>
<link href="https://fonts.googleapis.com/css2?family=Roboto:wght@400;700&display=swap" rel="stylesheet">
<style>
  :root {
    --bg: #111111;
    --white: #ffffff;
    --silver: #a9a9a9;
    --silver-light: #c4c4c4;
    --red: #c8102e;
  }
  html, body {
    margin: 0;
    padding: 0;
    overflow: hidden;
    background: var(--bg);
  }
  .back-cover {
    position: relative;
    width: 848px;
    height: 1200px;
    background: var(--bg);
    font-family: "Roboto", sans-serif;
    text-align: center;
    overflow: hidden;
  }
  .brand {
    position: absolute;
    top: 772px;
    left: 0;
    width: 100%;
    display: flex;
    justify-content: center;
    align-items: center;
    gap: 10px;
  }
  .brand-dot {
    width: 14px;
    height: 14px;
    border-radius: 50%;
    background: var(--red);
  }
  .brand-name {
    font-size: 38px;
    font-weight: 700;
    color: var(--white);
    letter-spacing: 1px;
    line-height: 1;
  }
  .office-title {
    position: absolute;
    top: 896px;
    left: 0;
    width: 100%;
    font-size: 20px;
    letter-spacing: 2px;
    color: var(--silver);
  }
  .office-address {
    position: absolute;
    top: 948px;
    left: 0;
    width: 100%;
    font-size: 16px;
    line-height: 26px;
    color: var(--silver);
    text-transform: uppercase;
  }
  .support-title {
    position: absolute;
    top: 1016px;
    left: 0;
    width: 100%;
    font-size: 18px;
    letter-spacing: 1.5px;
    color: var(--red);
  }
  .support-phones {
    position: absolute;
    top: 1045px;
    left: 0;
    width: 100%;
    font-size: 19px;
    color: var(--white);
  }
  .contact-line {
    position: absolute;
    top: 1097px;
    left: 0;
    width: 100%;
    font-size: 16px;
    color: var(--silver);
  }
  .contact-line .divider {
    margin: 0 12px;
  }
</style>
</head>
<body>
  <main class="back-cover">
    <div class="brand">
      <span class="brand-dot"></span>
      <span class="brand-name">TRUFLOW</span>
    </div>

    <div class="office-title">CORPORATE OFFICE</div>
    <div class="office-address">
      #48, Harbour View Lane, Eastbrook.<br>
      Westhaven. Australia. 204518
    </div>

    <div class="support-title">SUPPORT</div>
    <div class="support-phones">1800 555 0192, 1800 555 0347</div>

    <div class="contact-line">
      Email: help@truflowservices.com<span class="divider">|</span>Web: www.truflowservices.com
    </div>
  </main>
</body>
</html>
```